New Business Card Design Project

Use the flyer uploaded and website www.brightoakbuilders.com for inspiration.
List Our Services on Backside of business cards
Marcus Delling
Harborline Builders Inc.
Licensed General Contractors
858-471-6093

Contact Information for Business Card

Use the flyer uploaded and website www.brightoakbuilders.com for inspiration. List Our Services on Backside of business cards Marcus Delling Harborline Builders Inc. Licensed General Contractors 858-471-6093

```html
<!DOCTYPE html>
<html lang="en">
<head>
<meta charset="utf-8">
<title>Harborline Builders – Business Cards</title>
<link rel="stylesheet" href="https://fonts.googleapis.com/css2?family=Montserrat:wght@400;500&family=Oswald:wght@600&display=swap">
<style>
  :root {
    --backdrop: #1c1c1c;
    --card: #ffffff;
    --panel: #151515;
    --accent-red: #e3141f;
    --accent-blue: #2f7bd0;
    --ink: #1a1a1a;
    --logo-ink: #ffffff;
  }
  * { margin: 0; padding: 0; box-sizing: border-box; }
  html, body {
    width: 1200px; height: 1015px; overflow: hidden;
    background: var(--backdrop);
    font-family: "Montserrat", Arial, sans-serif;
  }
  .canvas { position: relative; width: 1200px; height: 1015px; }
  .card {
    position: absolute; left: 215px; width: 770px; height: 440px;
    background: var(--card); overflow: hidden;
    box-shadow: 0 12px 30px rgba(0,0,0,.55);
  }
  .card--back { top: 45px; }
  .card--front { top: 530px; }
  .card-art { position: absolute; inset: 0; width: 770px; height: 440px; }
  .brand {
    position: absolute; left: 642px; top: 318px; width: 122px;
    display: flex; flex-direction: column; align-items: flex-start; gap: 8px;
    color: var(--logo-ink); font-weight: 500; font-size: 12px; letter-spacing: 1.5px;
    text-transform: uppercase; line-height: 1.4;
  }
  .brand-dot { width: 10px; height: 10px; border-radius: 50%; background: var(--logo-ink); }
  .services {
    position: absolute; left: 60px; top: 228px; list-style: none;
    font-size: 16px; line-height: 21px; color: var(--ink);
  }
  .services li { position: relative; padding-left: 20px; }
  .services li::before {
    content: ""; position: absolute; left: 0; top: 7px;
    width: 8px; height: 8px; border-radius: 50%; background: var(--accent-red);
  }
  .person-name {
    position: absolute; left: 60px; top: 222px;
    font-family: "Oswald", "Arial Narrow", sans-serif; font-weight: 600;
    font-size: 42px; line-height: 54px; color: var(--accent-red); text-transform: uppercase; letter-spacing: -.5px;
  }
  .contact { position: absolute; left: 60px; top: 284px; list-style: none; font-size: 17px; line-height: 24px; color: var(--ink); }
  .contact li { display: flex; align-items: center; gap: 10px; }
  .contact svg { width: 17px; height: 17px; fill: var(--accent-blue); flex: none; }
  .company {
    position: absolute; left: 60px; top: 362px;
    font-size: 16px; line-height: 21px; font-weight: 500; color: var(--accent-red);
  }
</style>
</head>
<body>
<main class="canvas">

  <section class="card card--back">
    <svg class="card-art" viewBox="0 0 770 440">
      <defs>
        <linearGradient id="interiorGrey" x1="0" y1="1" x2="1" y2="0">
          <stop offset="0" stop-color="#6f7370"/>
          <stop offset=".45" stop-color="#d9d9d6"/>
          <stop offset="1" stop-color="#bdb8b2"/>
        </linearGradient>
      </defs>
      <polygon role="img" aria-label="Photo of a bright remodeled white bathroom" points="0,0 770,0 770,10 560,165 0,178" fill="url(#interiorGrey)"/>
      <polygon points="770,70 770,440 560,440 660,290 595,245" fill="var(--panel)"/>
      <polyline points="0,215 590,205 650,275 260,440" fill="none" stroke="var(--accent-blue)" stroke-width="2.5"/>
    </svg>
    <ul class="services">
      <li>Remodel: Kitchen &amp; Bath</li>
      <li>Painting: Interior &amp; Exterior</li>
      <li>Flooring: Carpet, Vinyl, Wood</li>
      <li>Window &amp; Door Replacement</li>
      <li>Plumbing: Repairs &amp; Upgrades</li>
      <li>Energy-Efficient Upgrades</li>
      <li>Deck &amp; Patio Construction</li>
      <li>Water &amp; Mold Damage</li>
      <li>Garage Renovation</li>
    </ul>
    <div class="brand"><span class="brand-dot"></span><span>Harborline<br>Builders</span></div>
  </section>

  <section class="card card--front">
    <svg class="card-art" viewBox="0 0 770 440">
      <defs>
        <linearGradient id="interiorWarm" x1="0" y1="1" x2="1" y2="0">
          <stop offset="0" stop-color="#c9923e"/>
          <stop offset=".4" stop-color="#e7cfa8"/>
          <stop offset=".7" stop-color="#e8e8ea"/>
          <stop offset="1" stop-color="#cfd0d4"/>
        </linearGradient>
      </defs>
      <polygon role="img" aria-label="Photo of a renovated kitchen with warm wood and white cabinets" points="0,0 770,0 770,10 560,165 0,178" fill="url(#interiorWarm)"/>
      <polygon points="770,70 770,440 560,440 660,290 595,245" fill="var(--panel)"/>
      <polyline points="0,215 590,205 650,275 260,440" fill="none" stroke="var(--accent-blue)" stroke-width="2.5"/>
    </svg>
    <h1 class="person-name">Marcus Delling</h1>
    <ul class="contact">
      <li><svg viewBox="0 0 24 24"><path d="M6.6 10.8a15 15 0 0 0 6.6 6.6l2.2-2.2a1 1 0 0 1 1-.25 11.4 11.4 0 0 0 3.6.6 1 1 0 0 1 1 1V20a1 1 0 0 1-1 1A17 17 0 0 1 3 4a1 1 0 0 1 1-1h3.5a1 1 0 0 1 1 1c0 1.25.2 2.45.6 3.6a1 1 0 0 1-.25 1z"/></svg>858-471-6093</li>
      <li><svg viewBox="0 0 24 24"><path d="M2 5h20v14H2z"/><path d="M2 5l10 8 10-8" fill="none" stroke="#fff" stroke-width="1.6"/></svg>info@brightoakbuilders.com</li>
      <li><svg viewBox="0 0 24 24"><circle cx="12" cy="12" r="10"/><path d="M2 12h20M12 2c3 3 3 17 0 20M12 2c-3 3-3 17 0 20" fill="none" stroke="#fff" stroke-width="1.4"/></svg>www.brightoakbuilders.com</li>
    </ul>
    <p class="company">Harborline Builders Inc.<br>Licensed General Contractors</p>
    <div class="brand"><span class="brand-dot"></span><span>Harborline<br>Builders</span></div>
  </section>

</main>
</body>
</html>
```